Business Card: RW Office Partners - Your organised problem solver

Business Name: RW Office Partners
Website: www.rwofficepartners.com.au
Email: marisol@rwofficepartners.com.au
Mobile: 61 482 907 236
Facebook: @rwofficepartners
Instrgram: @rwofficepartners

Brading Colours:
HEX
#986474
#ddccd3
#7a8498
#c9d8e4
#000000
#ffffff

Tag Line: Your organised problem solver

Link to DRAFT website:
https://deskhelpcollective.wixsite.com/rw-office-partners

About Page from the website:
My name is Marisol Wrenfield, and I would love to assist you to become more productive in your day to day and achieve your business and personal goals.
My mission is to give you time, time to work on the important tasks of your business or to be able to spend more time with your family. I will take on the tasks you don’t have time for, don’t know well or simply don’t like to do.
I have an extensive background in Administration, Tender Coordination, Document Control, WHS and Quality Management working primarily in the Construction, Mining and Corporate World.
I am passionate about being organised, having order and making things in your life (and mine) easier! I love to watch something unfold and grow into something amazing! I am known for being the go-to problem solver, the organiser of all things, producing high standards of work even under pressure. I’m also a confident communicator, and I understand that you’re busy running your business.

Target Market(s)

Small to Medium Business who require assistance in their business by a virtual assistant.

Industry/Entity Type

Virtual Assistant

Contact Information for Business Card

Mobile: 61 482 907 236

Font styles to use
Sans Serif

Colors
ffffff

Requirements
Must have
• Branding Colours as outlined.
Contact Details as outlined.
Logo as provided.
Proper contact details - mobile, facebook, instragm, website.
Simple, Elegant, very clean looking.
Should not have
• Note cute with pictures.
Not too girly as still want to market to construction companies.

```html
<!DOCTYPE html>
<html lang="en">
<head>
<meta charset="utf-8">
<title>RW Office Partners – Business Card</title>
<link href="https://fonts.googleapis.com/css2?family=Questrial&family=Arimo:wght@400&display=swap" rel="stylesheet">
<style>
  :root {
    --mauve: #986474;
    --slate: #7a8498;
    --white: #ffffff;
    --ink: #1f1f1f;
    --rule: #8a8f9c;
    --backdrop: #2a2a2a;
  }
  * { margin: 0; padding: 0; box-sizing: border-box; }
  html, body { width: 1200px; height: 1200px; overflow: hidden; }
  body { background: var(--backdrop); position: relative; font-family: "Arimo", Arial, sans-serif; }

  .card { position: absolute; top: 310px; height: 594px; }

  /* Front */
  .card-front { left: 234px; width: 364px; background: var(--white); text-align: center; }
  .brand-name {
    position: absolute; top: 128px; left: 0; right: 0;
    font-family: "Questrial", sans-serif; font-weight: 400; color: var(--slate);
    font-size: 42px; line-height: 46px; letter-spacing: 1px; text-transform: uppercase;
  }
  .person-name {
    position: absolute; top: 337px; left: 0; right: 0;
    font-family: "Questrial", sans-serif; color: var(--mauve);
    font-size: 21px; font-weight: 700; letter-spacing: 0.2px; text-transform: uppercase;
  }
  .divider { position: absolute; left: 87px; width: 190px; height: 26px; display: flex; align-items: center; justify-content: center; gap: 4px; }
  .divider::before, .divider::after { content: ""; flex: 1; height: 1px; background: var(--rule); }
  .divider-contact { top: 382px; }
  .divider-social { top: 495px; }
  .divider .icons { display: flex; gap: 5px; padding: 0 8px; }
  .icon-box { width: 24px; height: 24px; border-radius: 3px; background: var(--mauve); display: flex; align-items: center; justify-content: center; }
  .social-dot { width: 26px; height: 26px; border-radius: 50%; border: 1.5px solid var(--slate); }
  .contact-list { position: absolute; top: 418px; left: 0; right: 0; list-style: none; font-size: 16.5px; line-height: 22px; color: var(--ink); }
  .social-handle { position: absolute; top: 529px; left: 0; right: 0; font-size: 16.5px; color: var(--ink); }

  /* Back */
  .card-back { left: 627px; width: 369px; background: var(--slate); overflow: hidden; }
  .back-band { position: absolute; top: 0; left: 0; right: 0; height: 250px; background: var(--mauve); }
  .back-name {
    position: absolute; top: 200px; left: 0; right: 0; text-align: center;
    font-family: "Questrial", sans-serif; color: var(--white);
    font-size: 46px; line-height: 52px; text-transform: uppercase; letter-spacing: 1px;
  }
  .tagline {
    position: absolute; top: 492px; left: 0; right: 0; text-align: center;
    font-family: "Questrial", sans-serif; color: var(--white);
    font-size: 21px; line-height: 27px; font-weight: 700; text-transform: uppercase;
  }
</style>
</head>
<body>
  <section class="card card-front" aria-label="Business card front">
    <h1 class="brand-name">RW Office<br>Partners</h1>
    <p class="person-name">Marisol Wrenfield</p>
    <div class="divider divider-contact">
      <div class="icons">
        <span class="icon-box" aria-label="Phone">
          <svg width="16" height="14" viewBox="0 0 16 14"><path d="M2 5c0-3 12-3 12 0v1h-3V5H5v1H2z M4 7h8l2 6H2z" fill="#fff"/></svg>
        </span>
        <span class="icon-box" aria-label="Email">
          <svg width="16" height="12" viewBox="0 0 16 12"><rect x="1" y="1" width="14" height="10" fill="none" stroke="#fff" stroke-width="1.4"/><path d="M1 1l7 6 7-6" fill="none" stroke="#fff" stroke-width="1.4"/></svg>
        </span>
        <span class="icon-box" aria-label="Website">
          <svg width="16" height="16" viewBox="0 0 16 16"><circle cx="8" cy="8" r="6.5" fill="none" stroke="#fff" stroke-width="1.4"/><path d="M1.5 8h13M8 1.5c-3 3.5-3 9.5 0 13M8 1.5c3 3.5 3 9.5 0 13" fill="none" stroke="#fff" stroke-width="1.1"/></svg>
        </span>
      </div>
    </div>
    <ul class="contact-list">
      <li>61 482 907 236</li>
      <li>marisol@rwofficepartners.com.au</li>
      <li>www.rwofficepartners.com.au</li>
    </ul>
    <div class="divider divider-social">
      <div class="icons">
        <span class="social-dot" aria-label="Social profile"></span>
        <span class="social-dot" aria-label="Social profile"></span>
      </div>
    </div>
    <p class="social-handle">@rwofficepartners</p>
  </section>

  <section class="card card-back" aria-label="Business card back">
    <div class="back-band"></div>
    <p class="back-name">RW Office<br>Partners</p>
    <p class="tagline">Your organised<br>problem solver</p>
  </section>
</body>
</html>
```